Business Card Design Project

Industry/Entity Type

Business

Contact Information for Business Card

The Ardenfield Gospel Choir
Desmond Fairley, Minister of Music

The Grace Harbor Fellowship of Mount Orla
Founded 1792

Twitter @ardenfieldchoir
Instagram ardenfieldgc
Facebook socialhub-net.com/afgc382
Website: ardenfieldgc.org
For Bookings: (555) 274-AFGC
2748 Merrow Street, Halverston, ST 00412

Back of the Card
Music and Cd's Recordings Available On
Choirs Website and Also
Tunevault, Corvex Sound, Disc Sprout (the music online logo)

```html
<!DOCTYPE html>
<html lang="en">
<head>
<meta charset="utf-8">
<title>The Ardenfield Gospel Choir – Business Card</title>
<link rel="stylesheet" href="https://fonts.googleapis.com/css2?family=Roboto:wght@400;700&family=Roboto+Condensed:wght@400;700&family=Parisienne&display=swap">
<style>
  :root {
    --bg: #ecebe8;
    --red: #c8303b;
    --blue: #1a63ab;
    --blue-line: #2b5fae;
    --white: #ffffff;
    --paper: #f6f6f6;
    --grey-text: #555555;
  }
  * { box-sizing: border-box; margin: 0; padding: 0; }
  html, body { width: 1200px; height: 911px; overflow: hidden; background: var(--bg); }
  .canvas { position: relative; width: 1200px; height: 911px; }

  .card {
    position: absolute;
    width: 620px; height: 354px;
    border-radius: 16px;
    overflow: hidden;
    box-shadow: 0 6px 18px rgba(0,0,0,.18);
  }
  .card-front { left: 60px; top: 90px; background: var(--red); }
  .card-back  { left: 520px; top: 470px; background: radial-gradient(circle at 50% 30%, #2478c2, var(--blue) 70%); }

  .front-shape { position: absolute; inset: 0; }

  .identity {
    position: absolute; left: 24px; top: 36px; width: 340px;
    text-align: center;
  }
  .crest {
    display: inline-flex; align-items: center; gap: 6px;
    font: 700 14px 'Roboto', sans-serif; color: var(--blue);
    margin-bottom: 14px;
  }
  .crest-dot { width: 12px; height: 12px; border-radius: 50%; background: var(--blue); }
  .choir-name { font: 400 26px/1.1 'Parisienne', cursive; color: var(--red); white-space: nowrap; }
  .minister { font: 700 14px 'Roboto', sans-serif; color: var(--blue); margin-top: 8px; white-space: nowrap; }
  .church { font: 400 11px 'Roboto', sans-serif; color: var(--grey-text); margin-top: 5px; white-space: nowrap; }
  .founded { font: 400 11px 'Roboto', sans-serif; color: var(--grey-text); margin-top: 2px; }

  .contact {
    position: absolute; right: 22px; top: 30px;
    list-style: none; text-align: right;
    font: 400 13px/20px 'Roboto', sans-serif; color: var(--white);
  }
  .contact li { display: flex; justify-content: flex-end; align-items: center; gap: 8px; }
  .contact-icon { width: 11px; height: 11px; border-radius: 50%; background: var(--white); flex: none; }
  .contact svg { width: 12px; height: 12px; flex: none; }

  .person {
    position: absolute; left: 26px; bottom: 22px;
    color: var(--white); font: 400 13px/17px 'Roboto', sans-serif;
  }
  .person-name { font: 700 22px/24px 'Roboto Condensed', sans-serif; letter-spacing: .5px; }
  .person-title { font: 400 14px/18px 'Roboto Condensed', sans-serif; margin-bottom: 2px; }

  .back-content {
    position: absolute; inset: 0;
    display: flex; flex-direction: column; align-items: center; justify-content: center;
    color: var(--white);
  }
  .back-crest {
    display: inline-flex; align-items: center; gap: 8px;
    font: 700 18px 'Roboto', sans-serif; margin-bottom: 18px;
  }
  .back-crest-dot { width: 16px; height: 16px; border-radius: 50%; background: var(--white); }
  .availability { font: 400 26px/1.25 'Parisienne', cursive; text-align: center; }
  .stores { display: flex; gap: 14px; margin-top: 26px; list-style: none; }
  .store {
    border: 1.5px solid var(--white); border-radius: 14px;
    padding: 6px 16px; font: 700 13px 'Roboto', sans-serif;
  }
</style>
</head>
<body>
<main class="canvas">

  <section class="card card-front" aria-label="Business card front">
    <svg class="front-shape" viewBox="0 0 620 354" preserveAspectRatio="none" aria-hidden="true">
      <path d="M0 0 H410 C392 130 300 225 0 252 Z" fill="var(--paper)"/>
      <path d="M410 0 C392 130 300 225 0 252" fill="none" stroke="var(--blue-line)" stroke-width="4"/>
    </svg>

    <div class="identity">
      <div class="crest"><span class="crest-dot"></span>Ardenfield</div>
      <h1 class="choir-name">The Ardenfield Gospel Choir</h1>
      <p class="minister">Desmond Fairley, Minister of Music</p>
      <p class="church">The Grace Harbor Fellowship of Mount Orla</p>
      <p class="founded">Founded 1792</p>
    </div>

    <ul class="contact">
      <li>@ardenfieldchoir <span class="contact-icon"></span></li>
      <li>ardenfieldgc <span class="contact-icon"></span></li>
      <li>/afgc382 <span class="contact-icon"></span></li>
      <li>(555) 274-AFGC (Bookings)
        <svg viewBox="0 0 24 24" aria-hidden="true"><path fill="#fff" d="M6.6 10.8a15 15 0 0 0 6.6 6.6l2.2-2.2c.3-.3.7-.4 1-.2 1.1.4 2.3.6 3.6.6.6 0 1 .4 1 1V20c0 .6-.4 1-1 1A17 17 0 0 1 3 4c0-.6.4-1 1-1h3.5c.6 0 1 .4 1 1 0 1.3.2 2.5.6 3.6.1.3 0 .7-.2 1z"/></svg>
      </li>
      <li>www.ardenfieldgc.org
        <svg viewBox="0 0 24 24" aria-hidden="true"><circle cx="12" cy="12" r="9" fill="none" stroke="#fff" stroke-width="2.5"/><path d="M3 12h18M12 3c3 3 3 15 0 18M12 3c-3 3-3 15 0 18" fill="none" stroke="#fff" stroke-width="1.6"/></svg>
      </li>
    </ul>

    <div class="person">
      <p class="person-name">MARCUS HALE</p>
      <p class="person-title">CEO/FOUNDER</p>
      <p>2748 Merrow Street</p>
      <p>Halverston, ST 00412</p>
    </div>
  </section>

  <section class="card card-back" aria-label="Business card back">
    <div class="back-content">
      <div class="back-crest"><span class="back-crest-dot"></span>Ardenfield</div>
      <p class="availability">Music and Cd's Recordings Available On<br>Choirs Website and Also</p>
      <ul class="stores">
        <li class="store">Tunevault</li>
        <li class="store">Corvex Sound</li>
        <li class="store">Disc Sprout</li>
      </ul>
    </div>
  </section>

</main>
</body>
</html>
```